New Business Card Design Project

I need a design for business cards, i am an electrical business called "Corvane Electrical and Communications" i need the cards to be double sided with the company logo on the back (attached) the front needs to say my company name, web site, email address, telephone number, and ABN number and electrical license number. I am open to different arrangements of the information but would like the background to be incorporating something electrical or something that looks smart. open to all additional ideas also.

The company colours are orange and grey see logo attached.

Business Name: Corvane Electrical and Communications
Website: corvaneelectricalandcomms.example.com.au
Email: brent@corvaneelectricalandcomms.example.com.au
Telephone(mobile): 0481209736
ABN: 71208349162
Lic No: 418273D

Target Market(s)

Business entities, Project Managers, Accounts, Clients

Industry/Entity Type

Electrician

Contact Information for Business Card

I need a design for business cards, i am an electrical business called "Corvane Electrical and Communications" i need the cards to be double sided with the company logo on the back (attached) the front needs to say my company name

Font styles to use
Serif
Sans Serif

Colors
f37122
5c5c5c

Requirements
Must have
• Must have the Logo on the back open to different ways of it being on the back but had in mind to keep it central but again open to other options
Nice to have
• A real modern cool background that is eye catching yet contemporary
Should not have
• No backgrounds of a light bulb or plug or anything like that

```html
<!DOCTYPE html>
<html lang="en">
<head>
<meta charset="utf-8">
<title>Corvane Electrical and Communications – Business Card</title>
<link rel="stylesheet" href="https://fonts.googleapis.com/css2?family=Exo+2:wght@600;700&family=Arimo:wght@400&display=swap">
<style>
  :root {
    --backdrop: #3a3a3c;
    --card-grey: #59595b;
    --brand-orange: #f9ae1a;
    --text-white: #ffffff;
    --text-soft: #ececec;
  }
  * { box-sizing: border-box; margin: 0; padding: 0; }
  html, body { width: 1105px; height: 1200px; overflow: hidden; }
  body {
    background: var(--backdrop);
    position: relative;
    font-family: "Arimo", Arial, sans-serif;
  }
  .card {
    position: absolute;
    left: 196px;
    width: 720px;
    height: 412px;
    border-radius: 20px;
  }
  .card__frame {
    position: absolute;
    inset: 11px;
    border-radius: 22px;
    border: 3px solid;
  }
  .card--front { top: 146px; background: var(--card-grey); }
  .card--front .card__frame { border-color: var(--brand-orange); }
  .card--back { top: 602px; background: var(--brand-orange); }
  .card--back .card__frame { border-color: var(--text-white); }

  .brand-name {
    position: absolute;
    font-family: "Exo 2", Arial, sans-serif;
    font-weight: 700;
    color: var(--text-white);
  }
  .card--front .brand-name {
    right: 46px;
    top: 52px;
    text-align: right;
    font-size: 56px;
    line-height: 0.95;
    letter-spacing: 1px;
  }
  .card--front .brand-name small {
    display: block;
    font-size: 15px;
    letter-spacing: 0.6px;
    margin-top: 10px;
    text-transform: uppercase;
  }

  .holder { position: absolute; left: 48px; top: 108px; }
  .holder__name {
    font-family: "Exo 2", Arial, sans-serif;
    font-weight: 700;
    font-size: 27px;
    color: var(--brand-orange);
    line-height: 1.1;
  }
  .holder__role {
    font-family: "Exo 2", Arial, sans-serif;
    font-weight: 600;
    font-size: 19px;
    color: var(--text-white);
    margin-top: 2px;
  }
  .registration {
    position: absolute;
    left: 48px;
    top: 228px;
    font-size: 19px;
    line-height: 26px;
    color: var(--text-soft);
  }
  .contact-list {
    position: absolute;
    left: 48px;
    top: 294px;
    list-style: none;
    color: var(--text-soft);
  }
  .contact-list li {
    display: flex;
    align-items: center;
    gap: 9px;
    height: 28px;
    font-size: 16px;
  }
  .contact-list li.contact--phone { font-size: 19px; height: 32px; }
  .contact-list li.contact--web { font-size: 18px; }
  .contact-list svg { width: 18px; height: 18px; flex: none; }

  .card--back .brand-name {
    left: 0; right: 0;
    top: 168px;
    text-align: center;
    font-size: 64px;
    letter-spacing: 2px;
  }
  .card--back .website {
    position: absolute;
    left: 0; right: 0;
    top: 329px;
    text-align: center;
    font-size: 17px;
    letter-spacing: 1.6px;
    color: var(--text-white);
  }
</style>
</head>
<body>
  <section class="card card--front" aria-label="Business card front">
    <div class="card__frame"></div>
    <div class="brand-name">Corvane<small>Electrical &amp; Communications</small></div>

    <div class="holder">
      <p class="holder__name">Dale Harwick</p>
      <p class="holder__role">CEO/Founder</p>
    </div>

    <div class="registration">
      <p>ABN: 71208349162</p>
      <p>Lic No: 418273D</p>
    </div>

    <ul class="contact-list">
      <li class="contact--phone">
        <svg viewBox="0 0 18 18" aria-hidden="true"><rect x="4" y="1" width="10" height="16" rx="2" fill="none" stroke="#f9ae1a" stroke-width="2"/><rect x="7" y="13" width="4" height="1.6" fill="#f9ae1a"/></svg>
        0481209736
      </li>
      <li class="contact--email">
        <svg viewBox="0 0 18 18" aria-hidden="true"><rect x="1" y="4" width="16" height="11" rx="1.5" fill="#f9ae1a"/><path d="M1.5 4.8 9 10.5l7.5-5.7" fill="none" stroke="#59595b" stroke-width="1.4"/></svg>
        brent@corvaneelectricalandcomms.example.com.au
      </li>
      <li class="contact--web">
        <svg viewBox="0 0 18 18" aria-hidden="true"><circle cx="9" cy="9" r="8" fill="#f9ae1a"/><path d="M1 9h16M9 1c-3 3-3 13 0 16M9 1c3 3 3 13 0 16" fill="none" stroke="#59595b" stroke-width="1.2"/></svg>
        corvaneelectricalandcomms.example.com.au
      </li>
    </ul>
  </section>

  <section class="card card--back" aria-label="Business card back">
    <div class="card__frame"></div>
    <div class="brand-name">Corvane</div>
    <p class="website">www.corvaneelectricalandcomms.example.com.au</p>
  </section>
</body>
</html>
```